Create a Wordpress Design (Dorrel)

We need a wordpress design for an established auction and real estate company based in Tennessee. The winning design will incorporate a professional color scheme with company logo in a clean layout. The design needs to consider that this will be developed on a responsive theme. Colors are those that will highlight the logo.
Updates

This client, an older gentleman, wants the site to mimic http://www.quillfordbidhouse.example/. If you can adjust you designs with this site in mind - perhaps 3 columns, less color etc. We are trying to get him a concept that he likes and he keeps mentioning this site. Do not copy this site, but keep it in mind while re-doing the concept. Thanks, - auction services -

Industry/Entity Type

Real Estate

Font styles to use
Sans Serif

Colors

Designer to choose colors to be used in the design.

Requirements
Must have
• - Navigation: 1) Home - with auctions as content as seen at http://brenwickgavel.example/ 2) Properties for Sale 3) Auctions 4) Sell Your Property 5) Community Info 6) About Us 7) Contact Us

Color will be those that highlight logo in a professional creative way. Site tagline: "Our Signs are Everywhere". Site will have a slideshow - please use stock real estate image for the initial photo.

Widgets: 1) social media (FB twitter, linked In, Youtube, RSS) 2) News & Events blog, 3) testimonials 4) featured Property widget.

Footer will have contact info (below) smaller company logo, and the association logos attached, and contact info:
Phone: (615) 555-0178
Contacts: Marion Teague-Hollis
Email: marketing@kenwoodorrel.example
Address: 22-C Elmfield Court W, Ashbury Falls, TN 37199

Nice to have
• use and styling of a dropdown menu: Under AUCTIONS, 1) Upcoming 2) Past

```html
<!DOCTYPE html>
<html lang="en">
<head>
<meta charset="utf-8">
<title>Dorrel Commercial – Properties Auction</title>
<link href="https://fonts.googleapis.com/css2?family=Mulish:wght@400;600;700&family=Open+Sans:ital,wght@0,400;0,600;0,700;1,400&display=swap" rel="stylesheet">
<style>
:root{
  --red:#c4101a;
  --red-dark:#8e0a10;
  --red-deep:#6f0a0e;
  --orange:#f0a20a;
  --orange-text:#e39a0b;
  --ink:#222;
  --muted:#666;
  --line:#e2e2e2;
  --panel:#f4f3f1;
}
*{box-sizing:border-box;margin:0;padding:0}
html,body{width:1200px;height:2198px;overflow:hidden;background:#fff}
body{position:relative;font-family:"Open Sans",Arial,sans-serif;color:var(--ink)}
.abs{position:absolute}
a{color:inherit;text-decoration:none}

/* header */
.brand{left:110px;top:22px;display:flex;align-items:center;gap:14px}
.brand-mark{width:70px;height:70px;border-radius:50%;background:var(--red)}
.brand-name{font-family:"Mulish",sans-serif;font-weight:700;font-size:34px;color:var(--red);line-height:1}
.brand-sub{font-size:12px;color:var(--muted);margin-top:6px}
.header-contact{right:120px;top:56px;text-align:right;font-family:"Mulish",sans-serif}
.header-phone{font-size:25px;color:#333}
.header-email{font-size:15px;color:#555;margin-top:6px}

/* nav */
.main-nav{left:0;top:125px;width:1200px;height:51px;background:linear-gradient(#d5141f,#a80c14);display:flex;padding-left:123px}
.nav-item{font-family:"Mulish",sans-serif;font-weight:600;color:#fff;font-size:16px;padding:0 24px;line-height:51px;border-right:1px solid rgba(255,255,255,.3)}
.nav-item:last-child{border-right:0}
.nav-item.active{background:var(--red-dark)}
.dropdown{left:382px;top:176px;width:138px;background:var(--red-deep);padding:8px 0 6px}
.dropdown a{display:block;color:#fff;font-family:"Mulish",sans-serif;font-weight:600;font-size:14px;padding:7px 20px}
.dropdown a+a{border-top:1px solid rgba(255,255,255,.15)}

/* hero */
.hero{left:0;top:176px;width:1200px;height:454px;background:linear-gradient(180deg,#b9d3ea 0%,#dbe6ee 30%,#a9b99a 55%,#6f8b4e 80%,#e8e8e6 100%)}
.hero-caption{left:104px;top:306px;width:464px;height:184px;background:rgba(255,255,255,.88);padding:26px 24px 24px 50px}
.hero-kicker{font-family:"Mulish",sans-serif;color:var(--red);font-size:23px}
.hero-title{font-family:"Mulish",sans-serif;font-size:42px;color:#111;line-height:1.1;margin-top:2px}
.hero-text{font-size:12px;color:#888;line-height:1.75;margin-top:10px}
.hero-dots{left:564px;top:603px;display:flex;gap:4px}
.hero-dots span{width:14px;height:14px;border-radius:50%;background:#333}
.hero-dots span:first-child{background:var(--red)}

/* auctions */
.section-title{left:113px;top:674px;font-family:"Mulish",sans-serif;font-weight:400;font-size:22px;color:var(--orange-text)}
.auction{left:112px;width:672px;height:232px;border:1px solid var(--line);background:linear-gradient(#fff 75%,#f1f1f1);padding:26px 20px 0 21px;display:flex;gap:18px}
.auction-photo{width:210px;height:160px;flex:none}
.auction-title{font-family:"Mulish",sans-serif;font-weight:400;font-size:20px;color:var(--red);margin-top:2px}
.auction-sub{font-size:14.5px;color:#444;margin:3px 0 10px}
.auction-meta{font-size:12.5px;color:#444;line-height:26px}
.auction-meta b{font-weight:600}

/* sidebar */
.widget{left:808px;width:280px;border:1px solid var(--line);border-radius:4px;background:#fff;overflow:hidden}
.widget-head{height:54px;background:linear-gradient(#f6f6f6,#e9e9e9);font-family:"Mulish",sans-serif;font-size:21px;color:#333;padding:15px 26px}
.widget-head.orange{background:linear-gradient(#f8b315,#ee9a05);color:#fff}
.feature-main{padding:17px 16px 14px 23px;border-bottom:1px solid var(--line)}
.feature-photo{width:239px;height:121px}
.feature-title{font-family:"Mulish",sans-serif;color:var(--red);font-size:15.5px;margin-top:8px}
.feature-text{font-size:11.5px;color:#777}
.feature-row{display:flex;gap:12px;padding:14px 16px 12px 23px;border-bottom:1px solid var(--line)}
.feature-row:last-child{border-bottom:0}
.feature-thumb{width:88px;height:60px;flex:none;margin-top:6px}
.row-title{font-size:12px;color:var(--red)}
.row-date{font-size:11.5px;color:#555;margin-top:3px}
.row-text{font-size:10.5px;color:#aaa;line-height:1.45;margin-top:3px}
.news{padding:14px 24px 0 24px}
.news-item{margin-bottom:16px}
.news-title{font-size:13px;font-weight:600;color:var(--red)}
.news-text{font-size:11px;color:#666;line-height:1.55;margin-top:3px}
.news-more{font-size:11.5px;color:#333;margin-top:2px}
.quotes{padding:18px 24px}
.quote{font-size:11px;font-style:italic;color:#777;line-height:1.75}
.quote-by{font-size:11.5px;color:#444;margin:6px 0 24px}

/* footer */
.footer{left:0;top:1890px;width:1200px;height:245px;background:var(--panel)}
.footer-col{top:1934px;font-size:13px;color:#555;line-height:22.5px}
.footer-col h4{font-family:"Mulish",sans-serif;font-weight:400;font-size:20px;color:#333;margin-bottom:8px;line-height:1.2}
.badges{left:776px;top:1940px;width:310px;display:flex;flex-wrap:wrap;justify-content:flex-end;gap:18px 14px}
.badge{width:44px;height:38px;background:#444;border-radius:3px}
.badge.round{border-radius:50%;width:38px;height:38px}
.badge.wide{width:62px}
.bottom-bar{left:0;top:2135px;width:1200px;height:63px;background:#fff;border-top:1px solid #eaeaea}
.copyright{left:123px;top:2154px;font-size:12px;color:#666}
.social{left:946px;top:2151px;display:flex;gap:5px}
.social span{width:28px;height:28px;border-radius:50%;background:var(--red)}
</style>
</head>
<body>

<header>
  <div class="abs brand">
    <span class="brand-mark"></span>
    <div>
      <div class="brand-name">Dorrel Commercial</div>
      <div class="brand-sub">Realtors, Auctioneers · Kenwood Dorrel</div>
    </div>
  </div>
  <div class="abs header-contact">
    <div class="header-phone">(615) 555-0178</div>
    <div class="header-email">marketing@kenwoodorrel.example</div>
  </div>
</header>

<nav class="abs main-nav">
  <a class="nav-item">Home</a>
  <a class="nav-item">Properties for Sale</a>
  <a class="nav-item active">Auctions</a>
  <a class="nav-item">Sell Your Property</a>
  <a class="nav-item">Community Info</a>
  <a class="nav-item">About Us</a>
  <a class="nav-item">Contact Us</a>
</nav>

<section>
  <div class="abs hero" role="img" aria-label="Slideshow photo of a green weatherboard house with a white picket fence and hedges under a blue sky"></div>
  <div class="abs hero-caption">
    <div class="hero-kicker">Morbi porta libero ullamcorper</div>
    <div class="hero-title">Properties Auction</div>
    <p class="hero-text">Morbi porta libero id ullamcorper nonummy nibh ligula pulvinar<br>metus eget consectetuer augue nisi quis lacus Ut ac mi</p>
  </div>
  <div class="abs hero-dots"><span></span><span></span><span></span><span></span></div>
</section>

<div class="abs dropdown">
  <a>Upcoming</a>
  <a>Past</a>
</div>

<main>
  <h2 class="abs section-title">UPCOMING AUCTIONS</h2>

  <article class="abs auction" style="top:713px">
    <div class="auction-photo" role="img" aria-label="Modern house lit up at dusk with a pool" style="background:linear-gradient(#1d3f78,#2b5aa0 45%,#8a6a4a 75%,#3a3a40)"></div>
    <div>
      <h3 class="auction-title">Integer congue augue et malesuada</h3>
      <p class="auction-sub">Vivamus porttitor purus nisi eleifen</p>
      <div class="auction-meta">
        <div><b>Begins:</b> Thursday, June 25, 2015 at 1:00 PM EDT</div>
        <div><b>Ends:</b> Friday, June 26, 2015 at 1:00 PM EDT</div>
        <div>Click here for Online Bidding Click here for Online Bidding</div>
        <div><b>Location:</b> P.O. Box 40117 Halden, VA 24099</div>
      </div>
    </div>
  </article>

  <article class="abs auction" style="top:943px">
    <div class="auction-photo" role="img" aria-label="Two-storey grey shingle house with green lawn" style="background:linear-gradient(#c9d9e6,#9aa3a8 45%,#7d8a6a 75%,#5d7d3a)"></div>
    <div>
      <h3 class="auction-title">Etiam est nunc venenatis in tristique</h3>
      <p class="auction-sub">Vivamus porttitor purus nisi eleifen</p>
      <div class="auction-meta">
        <div><b>Begins:</b> Thursday, June 25, 2015 at 1:00 PM EDT</div>
        <div><b>Ends:</b> Friday, June 26, 2015 at 1:00 PM EDT</div>
        <div>Click here for Online Bidding Click here for Online Bidding</div>
        <div><b>Location:</b> P.O. Box 40117 Halden, VA 24099</div>
      </div>
    </div>
  </article>

  <article class="abs auction" style="top:1168px">
    <div class="auction-photo" role="img" aria-label="Craftsman style house with stone chimney and front path" style="background:linear-gradient(#6fa0d8,#8a8070 40%,#6c6a58 65%,#5a8a3a)"></div>
    <div>
      <h3 class="auction-title">Morbi porta libero ullamcorper nonummy</h3>
      <p class="auction-sub">Vivamus porttitor purus nisi eleifen</p>
      <div class="auction-meta">
        <div><b>Begins:</b> Thursday, June 25, 2015 at 1:00 PM EDT</div>
        <div><b>Ends:</b> Friday, June 26, 2015 at 1:00 PM EDT</div>
        <div>Click here for Online Bidding Click here for Online Bidding</div>
        <div><b>Location:</b> P.O. Box 40117 Halden, VA 24099</div>
      </div>
    </div>
  </article>

  <article class="abs auction" style="top:1398px">
    <div class="auction-photo" role="img" aria-label="Brick and stone family house with dark roof" style="background:linear-gradient(#dfe8f0,#7a6656 40%,#9a8472 65%,#6a9a3e)"></div>
    <div>
      <h3 class="auction-title">Vestibulum ligula augue bibendum</h3>
      <p class="auction-sub">Vivamus porttitor purus nisi eleifen</p>
      <div class="auction-meta">
        <div><b>Begins:</b> Thursday, June 25, 2015 at 1:00 PM EDT</div>
        <div><b>Ends:</b> Friday, June 26, 2015 at 1:00 PM EDT</div>
        <div>Click here for Online Bidding Click here for Online Bidding</div>
        <div><b>Location:</b> P.O. Box 40117 Halden, VA 24099</div>
      </div>
    </div>
  </article>

  <article class="abs auction" style="top:1623px">
    <div class="auction-photo" role="img" aria-label="Brick house among trees with a wide green lawn and a yard sign" style="background:linear-gradient(#b6cfe6,#5e7a4a 35%,#7a5040 50%,#6ea43e 70%,#7ab448)"></div>
    <div>
      <h3 class="auction-title">Vestibulum ligula augue bibendum</h3>
      <p class="auction-sub">Vivamus porttitor purus nisi eleifen</p>
      <div class="auction-meta">
        <div><b>Begins:</b> Thursday, June 25, 2015 at 1:00 PM EDT</div>
        <div><b>Ends:</b> Friday, June 26, 2015 at 1:00 PM EDT</div>
        <div>Click here for Online Bidding Click here for Online Bidding</div>
        <div><b>Location:</b> P.O. Box 40117 Halden, VA 24099</div>
      </div>
    </div>
  </article>
</main>

<aside>
  <div class="abs widget" style="top:661px;height:463px">
    <div class="widget-head">Featured Property</div>
    <div class="feature-main">
      <div class="feature-photo" role="img" aria-label="Featured two-storey house with gables and green lawn" style="background:linear-gradient(#c6dcef,#8c9486 45%,#6a7a5a 70%,#5e8a34)"></div>
      <div class="feature-title">Featured Property</div>
      <div class="feature-text">Cum sociis natoque penatibus et magnis</div>
    </div>
    <div class="feature-row">
      <div class="feature-thumb" role="img" aria-label="Grey single-storey house" style="background:linear-gradient(#cfdde8,#7a7f84 55%,#6a8a4a)"></div>
      <div>
        <div class="row-title">Auction Tittle Name</div>
        <div class="row-date">15 July 2014</div>
        <div class="row-text">Cum sociis natoque penati-<br>bus et magnis dis</div>
      </div>
    </div>
    <div class="feature-row">
      <div class="feature-thumb" role="img" aria-label="White house under blue sky" style="background:linear-gradient(#5e8fd0,#dfe6ee 55%,#6a9a3e)"></div>
      <div>
        <div class="row-title">Auction Tittle Name</div>
        <div class="row-date">15 July 2014</div>
        <div class="row-text">Cum sociis natoque penati-<br>bus et magnis dis</div>
      </div>
    </div>
  </div>

  <div class="abs widget" style="top:1150px;height:344px">
    <div class="widget-head orange">News &amp; Event Blog</div>
    <div class="news">
      <div class="news-item">
        <div class="news-title">Nunc porta convallis pede</div>
        <div class="news-text">Morbi eget arcu Morbi porta libero id ullam-<br>corper nonummy nibh ligula pulvinar</div>
        <div class="news-more">Read More</div>
      </div>
      <div class="news-item">
        <div class="news-title">Class aptent taciti</div>
        <div class="news-text">Donec scelerisque leo ac risus Praesent sit<br>amet est In dictum dolor eu dictum porttitor</div>
        <div class="news-more">Read More</div>
      </div>
      <div class="news-item">
        <div class="news-title">Curabitur vel mi sit amet magna</div>
        <div class="news-text">Donec scelerisque leo ac risus Praesent sit<br>amet est In dictum dolor eu dictum</div>
        <div class="news-more">Read More</div>
      </div>
    </div>
  </div>

  <div class="abs widget" style="top:1505px;height:345px">
    <div class="widget-head">Testimonials</div>
    <div class="quotes">
      <p class="quote">Etiam est nunc venenatis in tristique eu imperdiet ac nisl Cum sociis natoque penati-bus et magnis dis parturient montes nascetur ridiculus mus In iaculis facilisis massa</p>
      <p class="quote-by">By Author Name</p>
      <p class="quote">Morbi porta libero id ullamcorper nonummy nibh ligula pulvinar metus eget consectetuer augue nisi quis lacus Ut ac mi quis lacus mollis aliquam Curabitur iaculis tempus eros Curabitur vel mi sit amet magna</p>
      <p class="quote-by">By Author Name</p>
    </div>
  </div>
</aside>

<footer>
  <div class="abs footer"></div>
  <div class="abs footer-col" style="left:121px">
    <h4>Company</h4>
    <div>Home</div><div>Auctions</div><div>Real Estate Listings</div><div>Rentals</div><div>Our Team</div>
  </div>
  <div class="abs footer-col" style="left:307px">
    <h4>Sublinks</h4>
    <div>Curabitur vel mi sit</div><div>Amet magna malesuada</div><div>Ut nisi erat</div><div>Fermentum</div><div>Congue euismod</div>
  </div>
  <div class="abs footer-col" style="left:520px">
    <h4>Contact Info</h4>
    <div>Phone: (615) 555-0178</div>
    <div>Contacts: Marion Teague-Hollis</div>
    <div>Email: marketing@kenwoodorrel.example</div>
    <div>Address: 22-C Elmfield Court W,<br>Ashbury Falls, TN 37199</div>
  </div>
  <div class="abs badges">
    <span class="badge"></span><span class="badge"></span><span class="badge round"></span><span class="badge round"></span><span class="badge wide"></span>
    <span class="badge round"></span><span class="badge"></span><span class="badge wide"></span><span class="badge"></span>
  </div>
  <div class="abs bottom-bar"></div>
  <div class="abs copyright">© 2014 Company Name &nbsp;All right reserved &nbsp;Term of Use</div>
  <div class="abs social"><span></span><span></span><span></span><span></span></div>
</footer>

</body>
</html>
```